New website for out outstanding veterinary training center

We already have a beautiful logo with nice colors and we are now looking for a breathtaking modern website to present our training center and future corses held there. A section to book open courses should also be available.

We are planing the realize the website with Wordpress.
The following pages should be available:
- Startpage / Overview
- Page to present the different rooms and seating option
- Page where the rooms can be booked
- Page where recommended accommodation are presented
- Page to present and book corses
- contact page
- Impressum

Target Market(s)

European Union

Industry/Entity Type

Education, Veterinary medicine

Number of Pages Required

5+ page

Font styles to use
Sans Serif

Colors
00AB8E
00BBA5
67D7C9
C6EFE9
E9F9F6

Requirements
Must have
• The website must be clear and easy to read. The colors form the logos should be used for the design.
Should not have
• To playful design. The page is not for a veterinary practice. we are a training center for veterinarians!

```html
<!DOCTYPE html>
<html lang="en">
<head>
<meta charset="utf-8">
<title>Veterra Academy – Training Center</title>
<link href="https://fonts.googleapis.com/css2?family=Roboto:wght@400;500;700;900&display=swap" rel="stylesheet">
<style>
:root{
  --teal:#1c8676;
  --teal-bright:#00ab8e;
  --mint:#e9f9f6;
  --plum:#3f2f38;
  --ink:#3a2b33;
  --text:#6b6b6b;
  --white:#ffffff;
}
*{margin:0;padding:0;box-sizing:border-box}
html,body{width:1200px;height:3732px;overflow:hidden}
body{position:relative;font-family:'Roboto',sans-serif;background:var(--white);color:var(--ink)}
.abs{position:absolute}
.btn{position:absolute;display:flex;align-items:center;justify-content:center;gap:7px;background:var(--teal);color:var(--white);font-weight:500;font-size:14px;border-radius:22px;text-transform:uppercase;letter-spacing:.2px;white-space:nowrap}
.btn .dot{width:12px;height:12px;border-radius:50%;background:var(--white);position:relative}
.btn .dot::after{content:"";position:absolute;left:3px;top:3px;border-left:5px solid var(--teal);border-top:3px solid transparent;border-bottom:3px solid transparent}
.heading{font-weight:900;letter-spacing:-1.5px;text-transform:uppercase;line-height:1.07}
.heading .accent{color:var(--teal)}

/* header */
.site-header{left:0;top:0;width:1200px;height:104px;background:var(--white);z-index:3}
.brand-badge{left:140px;top:0;width:176px;height:163px;background:var(--white);border-radius:0 0 88px 88px;z-index:4;display:flex;flex-direction:column;align-items:center;justify-content:center;gap:8px}
.brand-badge .mark{width:56px;height:56px;border-radius:50%;background:var(--teal)}
.brand-badge .name{font-size:19px;font-weight:700;color:var(--teal)}
.nav{left:355px;top:40px;font-size:12.5px;font-weight:500;color:var(--ink)}
.nav a{position:absolute;white-space:nowrap;color:inherit;text-decoration:none}
.book-now{left:817px;top:28px;width:97px;height:39px;font-size:12px}
.call{left:932px;top:20px}
.call .label{display:flex;align-items:center;gap:8px;color:var(--teal);font-weight:700;font-size:19px}
.call .num{margin-top:6px;font-weight:700;font-size:17px;color:var(--ink)}

/* hero */
.hero{left:0;top:104px;width:1200px;height:674px;background:linear-gradient(180deg,#b9d7e4 0%,#8fb57a 30%,#5f9a3a 60%,#4b8a2b 100%)}
.hero-card{left:626px;top:284px;width:429px;height:268px;background:rgba(70,55,62,.82);border-radius:22px;text-align:center;color:var(--white)}
.hero-card h1{margin-top:40px;font-size:56px;font-weight:900;letter-spacing:-2px;text-transform:uppercase}
.hero-card p{margin-top:8px;font-size:21px}
.hero-card .btn{left:135px;top:180px;width:159px;height:38px}
.slide-arrow{width:38px;height:38px;border-radius:50%;background:rgba(40,30,35,.85);display:flex;align-items:center;justify-content:center}
.hero-edge{left:0;top:720px;width:1200px;height:60px}

/* about */
.about-mark{left:145px;top:866px;width:420px;height:440px;display:flex;align-items:center;justify-content:center;gap:14px}
.about-mark .mark{width:44px;height:44px;border-radius:50%;background:var(--teal);flex:none}
.about-mark .name{font-size:34px;font-weight:700;color:var(--teal);white-space:nowrap}
.about-title{left:636px;top:870px;font-size:56px}
.about-text{left:636px;top:1014px;width:420px;font-size:13.2px;line-height:25.6px;color:var(--text)}
.read-more{left:636px;top:1252px;width:159px;height:42px}

/* courses */
.courses-bg{left:0;top:1362px;width:1200px;height:826px}
.courses-title{left:0;top:1508px;width:1200px;text-align:center;font-size:58px}
.card{top:1627px;width:283px;height:349px;background:var(--white);border:1px solid #bcbcbc;text-align:center}
.card .photo{width:100%;height:180px}
.card h3{margin-top:32px;font-size:16.5px;font-weight:500;text-transform:uppercase;color:var(--ink)}
.card p{margin:18px auto 0;width:230px;font-size:13.3px;line-height:22.5px;color:var(--text)}
.card .btn{left:61px;top:329px;width:160px;height:42px}
.round-arrow{width:44px;height:44px;border-radius:50%;border:1.5px solid #555;background:var(--white);display:flex;align-items:center;justify-content:center}

/* accommodation */
.accom-title{left:0;top:2298px;width:1200px;text-align:center;font-size:58px}
.video-frame{left:210px;top:2549px;width:780px;height:485px;border:1.5px solid #d8d8d8;border-radius:12px;padding:5px;background:var(--white)}
.video{width:100%;height:100%;border-radius:8px;position:relative;background:linear-gradient(180deg,#5c7a45 0%,#6f9a4d 45%,#557f3a 100%)}
.play{left:304px;top:147px;width:180px;height:180px;border-radius:50%;border:9px solid var(--white);display:flex;align-items:center;justify-content:center}
.play .core{width:142px;height:142px;border-radius:50%;background:var(--teal);display:flex;align-items:center;justify-content:center}
.view-loc{left:287px;top:359px;width:193px;height:42px}

/* footer */
.footer-bg{left:0;top:3130px;width:1200px;height:602px}
.footer-title{font-size:17.5px;font-weight:700;color:var(--white)}
.field{position:absolute;background:var(--white);border:1px solid #aaa;font-size:10.5px;color:#555;padding:7px 11px;text-transform:uppercase}
.submit{left:609px;top:3572px;width:78px;height:26px;font-size:12px;font-weight:700}
.info-row{left:758px;display:flex;align-items:center;gap:17px;color:var(--white);font-size:11.5px;line-height:16px}
.info-icon{width:34px;height:34px;border-radius:50%;border:1.5px solid var(--white);display:flex;align-items:center;justify-content:center;flex:none}
.footer-rule{left:143px;top:3649px;width:914px;height:1px;background:#5a4a53}
.copyright{left:143px;top:3685px;font-size:11.5px;color:var(--white)}
.social{top:3678px;width:28px;height:28px;border-radius:50%;background:var(--teal-bright)}
</style>
</head>
<body>

<header class="abs site-header">
  <nav class="abs nav" aria-label="Main">
    <a style="left:0">OVERVIEW</a>
    <a style="left:88px">ROOMS</a>
    <a style="left:159px">ACCOMMODATION</a>
    <a style="left:294px">COURSES</a>
    <a style="left:378px">CONTACT</a>
  </nav>
  <span class="btn book-now">BOOK NOW</span>
  <div class="abs call">
    <div class="label">
      <svg width="34" height="34" viewBox="0 0 34 34"><circle cx="17" cy="17" r="15.5" fill="none" stroke="#1c8676" stroke-width="2"/><path d="M11 9c1-1 2.5-1 3 .2l1.3 3c.3.8 0 1.5-.6 2l-1 .8c.8 2 2.3 3.5 4.3 4.3l.8-1c.5-.6 1.2-.9 2-.6l3 1.3c1.2.5 1.2 2 .2 3l-1.3 1.3c-1 1-2.6 1.2-4 .5-4-2-7-5-9-9-.7-1.4-.5-3 .5-4z" fill="#1c8676"/></svg>
      CALL US
    </div>
    <div class="num">1 555 010 0199</div>
  </div>
</header>
<div class="abs brand-badge">
  <span class="mark"></span>
  <span class="name">Veterra Academy</span>
</div>

<section class="abs hero" role="img" aria-label="Photo: a young woman kneels on a lawn giving a high-five to a white dog wearing a green scarf"></section>
<div class="abs hero-card">
  <h1>Veterra</h1>
  <p>Sed ut perspiciatis undeisuptatem</p>
  <span class="btn">BOOK COURSES <span class="dot"></span></span>
</div>
<div class="abs slide-arrow" style="left:52px;top:400px"><svg width="12" height="14" viewBox="0 0 12 14"><path d="M8 2 3 7l5 5" fill="none" stroke="#fff" stroke-width="2"/></svg></div>
<div class="abs slide-arrow" style="left:1110px;top:400px"><svg width="12" height="14" viewBox="0 0 12 14"><path d="M4 2l5 5-5 5" fill="none" stroke="#fff" stroke-width="2"/></svg></div>
<svg class="abs hero-edge" viewBox="0 0 1200 60" preserveAspectRatio="none">
  <path d="M0 40 C300 70 900 70 1200 40 L1200 60 L0 60 Z" fill="#fff"/>
</svg>

<section>
  <div class="abs about-mark">
    <span class="mark"></span>
    <span class="name">Veterra Academy</span>
  </div>
  <h2 class="abs heading about-title">About<br><span class="accent">Veterra</span></h2>
  <p class="abs about-text">Lorem ipsum dolor sit amet, consectetur adipiscing elit, sed do eiusmod tempor incididunt ut labore et dolore magna aliqua.psum suspendisse ultrices grs commodo vmaecenas accumsan lacus vel facilisis. Lorem ipsum dolor sit amet, consectetur adipiscing elit, sed do eiusmod tempor incididunt ut labore et dolore magna aliqua.psum suspendisse ultrices grs commodo vmaecenas accumsan lacus vel facilisis. Lorem ipsum dolor sit amet, consectetur adipiscing elit, sed do eiusmod tempor incididunt ut lt dolore magna aliqua.</p>
  <span class="btn read-more">READ MORE <span class="dot"></span></span>
</section>

<section>
  <svg class="abs courses-bg" viewBox="0 0 1200 826" preserveAspectRatio="none">
    <path d="M0 160 C300 -40 900 -40 1200 160 L1200 660 C900 870 300 870 0 660 Z" fill="#e9f9f6"/>
  </svg>
  <h2 class="abs heading courses-title">Featured <span class="accent">Courses</span></h2>
  <div class="abs round-arrow" style="left:75px;top:1791px"><svg width="12" height="16" viewBox="0 0 12 16"><path d="M9 2 3 8l6 6" fill="none" stroke="#444" stroke-width="2"/></svg></div>
  <div class="abs round-arrow" style="left:1079px;top:1791px"><svg width="12" height="16" viewBox="0 0 12 16"><path d="M3 2l6 6-6 6" fill="none" stroke="#444" stroke-width="2"/></svg></div>

  <article class="abs card" style="left:151px">
    <div class="photo" role="img" aria-label="Photo: a woman walking a small dog on a forest path" style="background:linear-gradient(180deg,#5d6f3a,#8b7a4e)"></div>
    <h3>Inventore veritatis</h3>
    <p>Lorem ipsum dolor sit aconsectetur adipiscing elit, sed do eiusmod tempor incididunt ut</p>
    <span class="btn">BOOK NOW <span class="dot"></span></span>
  </article>
  <article class="abs card" style="left:458px">
    <div class="photo" role="img" aria-label="Photo: a trainer with a group of dogs sitting on grass" style="background:linear-gradient(180deg,#5f8c3e,#8a7458)"></div>
    <h3>Voluptatem</h3>
    <p>Lorem ipsum dolor sit aconsectetur adipiscing elit, sed do eiusmod tempor incididunt ut</p>
    <span class="btn">BOOK NOW <span class="dot"></span></span>
  </article>
  <article class="abs card" style="left:765px">
    <div class="photo" role="img" aria-label="Photo: a cat reaching up toward a person's hand by a window" style="background:linear-gradient(180deg,#d6d4d0,#8f877f)"></div>
    <h3>Eius modi</h3>
    <p>Lorem ipsum dolor sit aconsectetur adipiscing elit, sed do eiusmod tempor incididunt ut</p>
    <span class="btn">BOOK NOW <span class="dot"></span></span>
  </article>
</section>

<section>
  <h2 class="abs heading accom-title">Where recommended<br><span class="accent">accommodation are</span><br>presented</h2>
  <div class="abs video-frame">
    <div class="video" role="img" aria-label="Video still: a husky puppy on a leash sitting beside its owner on a lawn">
      <div class="abs play"><div class="core"><svg width="54" height="62" viewBox="0 0 54 62"><path d="M6 4 L50 31 L6 58 Z" fill="#fff" stroke="#fff" stroke-width="6" stroke-linejoin="round"/></svg></div></div>
      <span class="btn view-loc">VIEW LOCATIONS <span class="dot"></span></span>
    </div>
  </div>
</section>

<footer>
  <svg class="abs footer-bg" viewBox="0 0 1200 602" preserveAspectRatio="none">
    <path d="M0 20 C300 -5 900 -5 1200 20 L1200 602 L0 602 Z" fill="#3f2f38"/>
  </svg>
  <h4 class="abs footer-title" style="left:143px;top:3362px">Get In Touch</h4>
  <div class="field" style="left:145px;top:3405px;width:265px;height:29px">Name :</div>
  <div class="field" style="left:422px;top:3405px;width:265px;height:29px">Phone :</div>
  <div class="field" style="left:145px;top:3446px;width:542px;height:28px">Email :</div>
  <div class="field" style="left:145px;top:3485px;width:542px;height:66px">Message :</div>
  <span class="btn submit">SUBMIT</span>

  <h4 class="abs footer-title" style="left:758px;top:3362px">Contact Information</h4>
  <div class="abs info-row" style="top:3406px">
    <span class="info-icon"><svg width="12" height="16" viewBox="0 0 12 16"><path d="M6 1a5 5 0 0 0-5 5c0 4 5 9 5 9s5-5 5-9a5 5 0 0 0-5-5z" fill="none" stroke="#fff" stroke-width="1.5"/><circle cx="6" cy="6" r="1.8" fill="#fff"/></svg></span>
    <span>1223,Sed ut perspiciatis unde omnis<br>iste natus voluptatem sequi</span>
  </div>
  <div class="abs info-row" style="top:3453px">
    <span class="info-icon"><svg width="14" height="14" viewBox="0 0 14 14"><path d="M3 1c.6-.6 1.5-.5 1.8.2l.8 1.8c.2.5 0 1-.4 1.3l-.6.5c.5 1.2 1.4 2.1 2.6 2.6l.5-.6c.3-.4.8-.6 1.3-.4l1.8.8c.7.3.8 1.2.2 1.8l-.8.8c-.6.6-1.6.7-2.4.3-2.4-1.2-4.2-3-5.4-5.4-.4-.8-.3-1.8.3-2.4z" fill="#fff"/></svg></span>
    <span>Phone : 1 555 010 0199</span>
  </div>
  <div class="abs info-row" style="top:3500px">
    <span class="info-icon"><svg width="14" height="11" viewBox="0 0 14 11"><rect x="0" y="0" width="14" height="11" rx="1.5" fill="#fff"/><path d="M1 1.5 7 6l6-4.5" fill="none" stroke="#3f2f38" stroke-width="1.3"/></svg></span>
    <span>Email : info@veterra-academy.com</span>
  </div>
  <div class="abs info-row" style="top:3546px">
    <span class="info-icon"><svg width="15" height="15" viewBox="0 0 15 15"><circle cx="7.5" cy="7.5" r="6" fill="none" stroke="#fff" stroke-width="1.5"/><path d="M7.5 4v4h-2.5" fill="none" stroke="#fff" stroke-width="1.5"/></svg></span>
    <span style="font-size:17px;font-weight:700">24/7 Service</span>
  </div>

  <div class="abs footer-rule"></div>
  <p class="abs copyright">Copyrights © 2021, Veterra Academy.. All Rights Reserved.&nbsp; | &nbsp;Privacy policy&nbsp; | &nbsp;Impressum</p>
  <span class="abs social" style="left:890px" role="img" aria-label="Social profile"></span>
  <span class="abs social" style="left:924px" role="img" aria-label="Social profile"></span>
  <span class="abs social" style="left:958px" role="img" aria-label="Social profile"></span>
  <span class="abs social" style="left:992px" role="img" aria-label="Social profile"></span>
  <span class="abs social" style="left:1026px" role="img" aria-label="Social profile"></span>
</footer>

</body>
</html>
```